Business Cards for IT Consulting Company (Managed Service Provider)

I am looking to have some business cards printed and would like some designs. We are an IT Consulting company based in Vancouver BC. I would like a nice clean and modern look to the cards. I have uploaded all the versions of my logo so parts can be used as needed. Here is a snippit from our website homepage:

Quillbrook Networks Ltd. is an IT Solutions Partner located in Vancouver BC, Canada. We offer IT solutions and support to customers in the greater Vancouver Area. With expertise in Microsoft platforms, as well as Linux and Mac OSX and over 12 years experience in the IT industry, Quillbrook Networks is dedicated to offering our clients top quality service and products. We take pride in the solutions we offer our customers. The greatest compliment a client can give us is to recommend our services.

Quillbrook Networks Ltd. offers a wide range of IT services from onsite service to remote support and managed service solutions. This allows clients to choose the support path that best suits their company’s needs. Supporting many different sized companies from small to enterprise level over the past 12 years Quillbrook Networks has the experience and expertise needed to ensure things run smoothly. Allowing our clients to focus on doing business.

Revolutionizing the way IT services are delivered.

Quillbrook Networks is dedicated to providing our clients with IT solutions that work and grow with them for years to come. This philosophy helps save money in the long run instead of replacing equipment constantly. Far too often IT solutions are not well thought out and while possibly solving the problem at hand, require replacement due to growth or quality within a very short time frame. Quillbrook Networks takes pride in providing solutions that will last and be able to accommodate growth without the need for replacement.

Industry/Entity Type

Information Technology

Contact Information for Business Card

Quillbrook Networks Ltd.
(Employee Name)
Eml: (Employees Email Address)
Web: quillbrook.me
Ph: 604-555-0148

Font styles to use
Serif
Sans Serif

Requirements
Must have
• The Company logo and company colors.
Nice to have
• - Our tag line: "Revolutionizing IT Services" or "Revolutionizing the way IT services are delivered."
• - Also I really like the idea of nature and technology together blending which is sort of where my logo came from so integrating that somehow onto the business cards would be great.

```html
<!DOCTYPE html>
<html lang="en">
<head>
<meta charset="utf-8">
<title>Quillbrook Networks Ltd. — Business Card</title>
<link rel="stylesheet" href="https://fonts.googleapis.com/css2?family=Montserrat:wght@400;600;700;800&display=swap">
<style>
  :root {
    --page-bg: #e9e9eb;
    --card-dark: #121515;
    --pattern-line: #3a3d3e;
    --card-light: #ffffff;
    --brand-cyan: #12aee6;
    --brand-grey: #6b6d6f;
    --band-grey: #858789;
    --text-dark: #4a4b4d;
  }
  * { box-sizing: border-box; margin: 0; padding: 0; }
  html, body {
    width: 1200px; height: 1200px; overflow: hidden;
    background: var(--page-bg);
    font-family: "Montserrat", Arial, sans-serif;
  }
  .canvas { position: relative; width: 1200px; height: 1200px; }

  .card {
    position: absolute; width: 760px; height: 440px;
    overflow: hidden; border-radius: 4px;
    box-shadow: 0 12px 30px rgba(0,0,0,0.18);
  }

  /* Card back */
  .card-back { left: 110px; top: 130px; background: var(--card-dark); }
  .card-back .pattern-fill {
    position: absolute; inset: 0;
    background: radial-gradient(circle at 60% 40%, #2a2d2e 0%, var(--card-dark) 75%);
  }
  .card-back .wordmark {
    position: absolute; left: 90px; top: 250px;
    display: flex; align-items: center; gap: 22px;
  }
  .wordmark .mark-dot {
    width: 70px; height: 70px; border-radius: 50%;
    border: 5px solid var(--brand-cyan);
  }
  .wordmark .brand-name {
    color: var(--brand-cyan); font-weight: 700;
    font-size: 40px; line-height: 1.05; letter-spacing: 0.5px;
  }

  /* Card front */
  .card-front { left: 330px; top: 640px; background: var(--card-light); }
  .card-front .wordmark {
    position: absolute; right: 40px; top: 48px;
    display: flex; align-items: center; gap: 14px;
  }
  .card-front .wordmark .mark-dot { width: 40px; height: 40px; border-width: 3px; }
  .card-front .wordmark .brand-name { font-size: 26px; }

  .person { position: absolute; left: 370px; top: 220px; }
  .person-name {
    color: var(--brand-cyan); font-weight: 800; font-size: 26px; letter-spacing: 1.5px;
  }
  .person-title {
    color: var(--text-dark); font-weight: 700; font-size: 14px; letter-spacing: 1px; margin-top: 2px;
  }
  .contact-list { list-style: none; margin-top: 18px; }
  .contact-list li {
    display: flex; align-items: center; gap: 12px;
    color: var(--text-dark); font-size: 17px; margin-bottom: 8px;
  }
  .contact-icon { width: 18px; height: 18px; flex: none; }

  .footer-band {
    position: absolute; left: 0; right: 0; bottom: 0; height: 72px;
  }
  .footer-band svg { position: absolute; inset: 0; width: 100%; height: 100%; }
  .web-address {
    position: absolute; left: 90px; bottom: 22px;
    color: #ffffff; font-size: 18px; font-weight: 400;
  }
</style>
</head>
<body>
<main class="canvas">

  <section class="card card-back" aria-label="Business card back">
    <div class="pattern-fill" role="img" aria-label="Dark background with a subtle repeating geometric line pattern"></div>
    <div class="wordmark">
      <span class="mark-dot"></span>
      <span class="brand-name">Quillbrook<br>Networks Ltd.</span>
    </div>
  </section>

  <section class="card card-front" aria-label="Business card front">
    <div class="wordmark">
      <span class="mark-dot"></span>
      <span class="brand-name">Quillbrook<br>Networks Ltd.</span>
    </div>

    <div class="person">
      <p class="person-name">DANA WHITFIELD</p>
      <p class="person-title">DIRECTOR</p>
      <ul class="contact-list">
        <li>
          <svg class="contact-icon" viewBox="0 0 18 18" aria-hidden="true">
            <rect width="18" height="18" rx="3" fill="var(--brand-cyan)"/>
            <path d="M5 4.5c.8-.5 1.5-.3 2 .6l.8 1.4c.3.6.1 1.1-.4 1.4l-.6.4c.6 1.3 1.5 2.2 2.8 2.8l.4-.6c.3-.5.8-.7 1.4-.4l1.4.8c.9.5 1.1 1.2.6 2-.8 1.1-2 1.4-3.4.8-2.5-1.1-4.4-3-5.5-5.5C3.9 6.6 4 5.3 5 4.5z" fill="#fff"/>
          </svg>
          604-555-0148
        </li>
        <li>
          <svg class="contact-icon" viewBox="0 0 18 18" aria-hidden="true">
            <rect width="18" height="18" rx="3" fill="var(--brand-cyan)"/>
            <rect x="5.5" y="3" width="7" height="12" rx="1.2" fill="none" stroke="#fff" stroke-width="1.5"/>
            <circle cx="9" cy="12.8" r="0.9" fill="#fff"/>
          </svg>
          604-555-0172
        </li>
        <li>
          <svg class="contact-icon" viewBox="0 0 18 18" aria-hidden="true">
            <rect width="18" height="18" rx="3" fill="var(--brand-cyan)"/>
            <rect x="3.5" y="5" width="11" height="8" fill="none" stroke="#fff" stroke-width="1.4"/>
            <path d="M3.5 5l5.5 4.5L14.5 5" fill="none" stroke="#fff" stroke-width="1.4"/>
          </svg>
          danawhitfield@quillbrook.me
        </li>
      </ul>
    </div>

    <div class="footer-band">
      <svg viewBox="0 0 760 72" preserveAspectRatio="none" aria-hidden="true">
        <polygon points="0,0 300,0 330,72 0,72" fill="var(--brand-cyan)"/>
        <polygon points="300,0 760,0 760,72 330,72" fill="var(--band-grey)"/>
      </svg>
      <span class="web-address">quillbrook.me</span>
    </div>
  </section>

</main>
</body>
</html>
```